Professional Engineering Web Design

Project Brief: Website Redesign for Mechanical Design Consultancy
Project Overview
I want to update and improve my current website to create a more professional, modern, and high-credibility online presence for my mechanical design consultancy.

Current site: https://valtorix.design/

The new website must communicate expertise, precision, and trust—matching the standard of top engineering and product design agencies.

Reference Websites (Style + Structure Inspiration)
These represent the quality, cleanliness, and professionalism I want to achieve:

https://plinthwaredesign.com/
https://www.sorvane.com/
https://bramlow-uk.com/
Brand Look
Professional, modern, engineering-focused aesthetic
Clean layouts and strong typography
High-quality imagery conveying precision, innovation, and mechanical expertise
Colour scheme and styling must follow my existing logo (attached in project)
Platform Requirements
The website must be built on WordPress
Should use a clean, flexible theme or modern page builder (Elementor, Gutenberg, Bricks, or similar)
Avoid overly complex custom coding so I can easily edit content later
Final deliverable must allow me to manage and update content without developer assistance
Functionality
Fast-loading, lightweight, and smooth user experience
Clean animations and transitions similar to the reference sites
Fully mobile responsive
Clear navigation and strong visual hierarchy
Contact forms optimised for lead generation
Optional: subtle scroll effects, case study sliders, icon animations, etc.
SEO Aspirations
Developer should recommend and implement a modern SEO strategy
Proper on-page SEO setup (titles, meta, schema, alt tags, heading structure)
Optimised site architecture for ranking and crawling
Aim: Generate leads through improved visibility and keyword targeting
Optional but useful: Northfield Analytics, Northfield Search Console setup
User Journeys
(Recommended structure)

The site should be crafted around clear, intuitive journeys for each type of visitor:

Potential new clients
Quickly understand what services I offer
View examples of past work / case studies
See credibility indicators (process, expertise, industries served)
Easily contact me or request a project discussion
Returning clients
Access updated portfolio items
Find contact details or book follow-up work easily
General visitors discovering through SEO
Be guided to core service areas
Understand my value proposition quickly
Be invited to learn more or make contact
The developer should design the structure to support these journeys smoothly.

Maintenance Expectations
Website will be maintained by me, so it should be easy to update using relatively basic WordPress skills
Use modular templates and simple backend structure
Avoid unnecessary plugins
Provide brief handover documentation if required
Hosting Preferences
Site is currently hosted via a family member
Open to discussing moving to a paid, reliable hosting provider if preferable for performance and maintainability
Developer may advise on the best hosting setup for WordPress
Content
Most content can be taken from the existing website
Developer is welcome to suggest improvements to structure, layout, and imagery
Must remain easy for me to edit or add new content later (e.g., new projects)
Deliverables
Fully built WordPress website
Clean, professional, modern design inspired by the reference sites
Mobile-responsive across all devices
SEO-ready structure and optimisations
Transfer of website and admin rights
Any design assets, templates, or documentation used

```html
<!DOCTYPE html>
<html lang="en">
<head>
<meta charset="utf-8">
<title>Valtorix Mechanical Design — Precision Mechanical Engineering Solutions</title>
<link rel="stylesheet" href="https://fonts.googleapis.com/css2?family=Poppins:wght@300;400;500;600;700&display=swap">
<style>
:root{
  --blue:#3b6ef2;
  --blue-dark:#2c58d6;
  --ink:#2a2a2d;
  --text:#4a4d55;
  --muted:#7a7e88;
  --line:#d9dce3;
  --soft:#f3f4f7;
  --white:#ffffff;
  --footer:#232427;
}
*{box-sizing:border-box;margin:0;padding:0}
html,body{width:1200px;height:4706px;overflow:hidden}
body{font-family:"Poppins",sans-serif;color:var(--text);background:var(--white);position:relative}
.abs{position:absolute}
a{color:inherit;text-decoration:none}

/* top bar */
.topbar{left:0;top:0;width:1200px;height:27px;background:var(--blue);color:#fff;font-size:11px;display:flex;justify-content:center;gap:52px;align-items:center}
.topbar span{display:flex;align-items:center;gap:8px}
.topbar svg{width:12px;height:12px;fill:#fff}

/* nav */
.nav{left:0;top:27px;width:1200px;height:79px;background:#fff}
.brand{display:flex;align-items:center;gap:10px;font-family:"Poppins",sans-serif;font-weight:500;font-size:30px;letter-spacing:3px;color:var(--ink)}
.brand .dot{width:46px;height:46px;border-radius:50%;background:var(--blue)}
.nav .brand{left:141px;top:16px}
.menu{left:468px;top:32px;display:flex;gap:22px;font-size:12px;color:var(--muted)}
.menu .active{color:var(--ink);border-bottom:2px solid var(--blue);padding-bottom:5px}
.search{left:840px;top:30px;font-size:12px;color:var(--muted);display:flex;gap:8px;align-items:center}
.pill{display:flex;align-items:center;justify-content:space-between;border-radius:22px;font-size:12px;color:#fff;padding:0 5px 0 18px;white-space:nowrap}
.pill .ring{width:30px;height:30px;border-radius:50%;background:#fff;display:flex;align-items:center;justify-content:center}
.pill .ring svg{width:15px;height:15px;fill:var(--ink)}
.pill.blue .ring svg{fill:var(--blue)}
.pill.dark{background:var(--ink)}
.pill.blue{background:var(--blue)}
.nav .pill{left:932px;top:22px;width:126px;height:38px}

/* hero */
.hero{left:0;top:106px;width:1200px;height:616px;background:linear-gradient(110deg,#2d3135 0%,#4a5056 45%,#6c7278 70%,#3d4247 100%)}
.hero h1{left:141px;top:70px;color:#fff;font-weight:300;font-size:36px;line-height:1.3}
.hero h1 strong{display:block;font-weight:600;font-size:56px;line-height:1.3}
.hero p{left:141px;top:285px;width:380px;color:#fff;font-size:16px;line-height:29px}
.hero .pill{left:141px;top:410px;width:194px;height:42px;font-size:13px}
.wave{left:0;top:600px;width:1200px;height:140px}
.mouse{left:568px;top:680px;width:64px;height:64px;border-radius:50%;background:#fff;box-shadow:0 4px 14px rgba(0,0,0,.12);display:flex;align-items:center;justify-content:center}

/* headings */
.eyebrow-mark{display:flex;align-items:center;gap:10px}
.eyebrow-mark i{display:block;width:55px;height:2px;background:var(--line)}
.eyebrow-mark b{width:18px;height:18px;border-radius:50%;border:4px solid var(--blue);display:block}
.sec-title{width:1200px;left:0;text-align:center;font-size:24px;font-weight:500;color:var(--ink)}
.sec-mark{left:0;width:1200px;display:flex;justify-content:center}
.sec-sub{width:1200px;left:0;text-align:center;font-size:15px;color:var(--text)}

/* about */
.photo{border-radius:4px}
.about-main{left:141px;top:826px;width:394px;height:358px;background:linear-gradient(135deg,#c9ced4,#7d858d 60%,#4b5158)}
.about-small{left:352px;top:1005px;width:212px;height:210px;background:linear-gradient(160deg,#d7d9dc,#9a8f85 60%,#5d5852);border:5px solid #fff}
.about-badge{left:323px;top:975px;width:56px;height:56px;border-radius:50%;background:#fff;border:8px solid var(--blue)}
.about h2{left:608px;top:828px;font-size:24px;font-weight:500;color:var(--ink)}
.about .eyebrow-mark{position:absolute;left:608px;top:873px}
.about p{left:608px;top:908px;width:450px;font-size:15px;line-height:30px}
.ticks{left:608px;top:1104px;display:flex;gap:40px;font-size:15px;color:var(--ink)}
.ticks span{display:flex;gap:10px;align-items:center}
.tick{width:18px;height:18px;border-radius:50%;background:var(--blue);display:flex;align-items:center;justify-content:center}
.about .pill{left:608px;top:1169px;width:232px;height:44px}

/* grey bands */
.band{left:0;width:1200px;background:var(--soft)}

/* service cards */
.card{background:#fff;border-radius:6px;box-shadow:0 6px 20px rgba(30,40,70,.07)}
.svc{top:1534px;width:283px;height:384px;text-align:center}
.svc .ico{margin:28px auto 0;width:64px;height:64px;border-radius:50%;background:var(--blue);display:flex;align-items:center;justify-content:center}
.svc .ico.dark{background:var(--ink)}
.svc .ico svg{width:32px;height:32px;stroke:#fff;fill:none;stroke-width:1.6}
.svc h3{margin-top:20px;font-size:16px;font-weight:600;color:var(--ink);white-space:nowrap}
.svc p{margin:8px auto 0;width:270px;font-size:12.5px;line-height:24px;white-space:nowrap}
.svc .img{position:absolute;left:15px;bottom:15px;width:253px;height:162px;border-radius:4px}

/* case cards */
.case{top:2214px;width:283px;height:339px;overflow:hidden}
.case .img{height:164px;background:linear-gradient(180deg,#f2f2f2,#cfd1d4)}
.case h3{margin:18px 17px 0;font-size:15px;font-weight:500;color:var(--ink)}
.case p{margin:8px 17px 0;font-size:12px;line-height:22px;white-space:nowrap}
.case .more{position:absolute;left:17px;top:300px;font-size:12px;color:var(--ink);display:flex;gap:8px;align-items:center}
.more svg{width:18px;height:10px;stroke:var(--blue);fill:none;stroke-width:1.6}

/* process */
.step{top:2941px;width:212px;height:233px;padding:22px 17px}
.step .head{display:flex;align-items:center;gap:12px;font-size:15px;color:var(--ink);font-weight:500}
.step .ico{width:46px;height:46px;border-radius:50%;background:var(--blue);display:flex;align-items:center;justify-content:center}
.step .ico svg{width:24px;height:24px;stroke:#fff;fill:none;stroke-width:1.6}
.step p{margin-top:18px;font-size:11.5px;line-height:22px;white-space:nowrap}
.step .more{position:absolute;left:17px;top:195px;font-size:12px;color:var(--ink);display:flex;gap:8px;align-items:center}
.step .num{position:absolute;right:14px;top:180px;font-size:42px;font-weight:700;color:#eef0f4;line-height:1}

/* testimonial */
.quote-name{left:194px;top:3360px;font-size:28px;font-weight:600;color:var(--ink)}
.quote-role{left:194px;top:3398px;font-size:13px;color:var(--text)}
.qmark{font-size:56px;font-weight:700;color:var(--blue);line-height:1}
.quote-text{left:194px;top:3472px;width:520px;font-size:13px;line-height:25.5px}
.portrait{left:771px;top:3353px;width:234px;height:234px;border-radius:50%;background:linear-gradient(160deg,#e8e8ea,#b9a89a 55%,#7a6a5e);border:3px solid #fff;box-shadow:-6px 0 0 0 var(--blue)}
.socials{left:832px;top:3610px;display:flex;gap:10px}
.round{display:block;width:30px;height:30px;border-radius:50%;border:1px solid var(--line);background:#fff}
.round.on{background:var(--blue);border-color:var(--blue)}
.arrow-btn{width:28px;height:28px;border-radius:50%;display:flex;align-items:center;justify-content:center}
.arrow-btn svg{width:12px;height:12px;stroke:#fff;fill:none;stroke-width:2}
.dots{left:572px;top:3660px;display:flex;gap:7px}
.dots i{width:7px;height:7px;border-radius:50%;background:#cfd3dc}
.dots i.on{background:var(--blue)}

/* contact */
.contact-bg{left:0;top:3726px;width:1200px;height:600px}
.contact h2{left:177px;top:3878px;font-size:26px;font-weight:600;color:#fff}
.contact .lead{left:177px;top:3936px;font-size:11.5px;line-height:24px;color:#e6ecff;white-space:nowrap}
.line-item{left:177px;display:flex;gap:15px;color:#fff;font-size:14px;line-height:26px}
.line-item .c{width:30px;height:30px;border-radius:50%;background:#fff;display:flex;align-items:center;justify-content:center;margin-top:10px}
.line-item .c svg{width:15px;height:15px;fill:var(--blue)}
.form{left:586px;top:3850px;width:437px;height:455px;background:#fff;border-radius:6px;box-shadow:0 10px 30px rgba(0,0,0,.12);padding:30px 24px}
.form h3{font-size:22px;font-weight:600;color:var(--ink);margin-bottom:20px}
.form h3 span{color:var(--blue)}
.field{height:40px;border:1px solid var(--line);border-radius:5px;font-size:11px;color:var(--muted);padding:12px 16px;margin-bottom:13px}
.field.msg{height:119px}
.submit{height:44px;border-radius:22px;background:var(--blue);color:#fff;font-size:13px;display:flex;align-items:center;justify-content:center;gap:14px}
.submit svg{width:20px;height:10px;stroke:#fff;fill:none;stroke-width:1.8}

/* footer */
.footer{left:0;top:4274px;width:1200px;height:432px;background:var(--footer);color:#fff}
.footer .brand{color:#fff;position:absolute;left:505px;top:100px}
.footer .desc{left:180px;top:172px;width:840px;text-align:center;font-size:12px;line-height:23px;color:#d6d8dd}
.fnav{left:0;width:1200px;top:248px;display:flex;justify-content:center;font-size:12px}
.fnav a{padding:0 28px;border-right:1px solid #55575c}
.fnav a:last-child{border-right:0}
.fline{left:141px;top:305px;width:918px;height:1px;background:#3c3e43}
.fcontacts{left:0;width:1200px;top:332px;display:flex;justify-content:center;gap:106px;font-size:12px}
.fcontacts span{display:flex;gap:10px;align-items:center}
.fcontacts svg{width:14px;height:14px;fill:#fff}
.copy{left:141px;top:398px;font-size:11px;color:#cfd1d6}
.fsocial{left:930px;top:392px;display:flex;gap:14px}
.fsocial i{display:block;width:20px;height:20px;border-radius:50%;background:#4a4c52}
.fsocial i.on{background:var(--blue)}
</style>
</head>
<body>
<svg width="0" height="0" style="position:absolute">
  <defs>
    <symbol id="i-phone" viewBox="0 0 24 24"><path d="M6.6 10.8a15.2 15.2 0 0 0 6.6 6.6l2.2-2.2c.3-.3.7-.4 1-.2 1.1.4 2.3.6 3.6.6.6 0 1 .4 1 1V20c0 .6-.4 1-1 1A17 17 0 0 1 3 4c0-.6.4-1 1-1h3.5c.6 0 1 .4 1 1 0 1.3.2 2.5.6 3.6.1.3 0 .7-.2 1z"/></symbol>
    <symbol id="i-pin" viewBox="0 0 24 24"><path d="M12 2a7 7 0 0 0-7 7c0 5.2 7 13 7 13s7-7.8 7-13a7 7 0 0 0-7-7zm0 9.5A2.5 2.5 0 1 1 12 6.5a2.5 2.5 0 0 1 0 5z"/></symbol>
    <symbol id="i-mail" viewBox="0 0 24 24"><path d="M3 5h18a1 1 0 0 1 1 1v12a1 1 0 0 1-1 1H3a1 1 0 0 1-1-1V6a1 1 0 0 1 1-1zm9 7.5L20 7H4z"/></symbol>
    <symbol id="i-arrow" viewBox="0 0 20 10"><path d="M0 5h18M14 1l4 4-4 4"/></symbol>
  </defs>
</svg>

<!-- top bar -->
<div class="abs topbar">
  <span><svg><use href="#i-pin"/></svg>Location: We're based in South Wales, UK.</span>
  <span><svg><use href="#i-phone"/></svg>Phone: +44 (0) 7700 900418</span>
  <span><svg><use href="#i-mail"/></svg>Email: info@valtorix.design</span>
</div>

<!-- navigation -->
<header class="abs nav">
  <div class="abs brand"><span class="dot"></span>valtorix</div>
  <nav class="abs menu"><a class="active">Home</a><a>About Us</a><a>Services</a><a>Portfolio</a><a>Process</a></nav>
  <div class="abs search"><svg width="14" height="14" viewBox="0 0 24 24" fill="none" stroke="#7a7e88" stroke-width="2"><circle cx="10" cy="10" r="7"/><path d="M15 15l6 6"/></svg>Search...</div>
  <a class="abs pill dark">Contact Us<span class="ring"><svg><use href="#i-phone"/></svg></span></a>
</header>

<!-- hero -->
<section class="abs hero" role="img" aria-label="Engineer working at CAD workstations showing mechanical part models">
  <h1 class="abs">Precision Mechanical<strong>Engineering<br>Solutions</strong></h1>
  <p class="abs">Transforming concepts into production-ready designs with expertise and innovation</p>
  <a class="abs pill blue">Start Your Project<span class="ring"><svg><use href="#i-phone"/></svg></span></a>
</section>
<svg class="abs wave" viewBox="0 0 1200 140" preserveAspectRatio="none">
  <path d="M0 60 Q600 150 1200 55 L1200 140 L0 140Z" fill="#fff"/>
  <path d="M0 60 Q600 150 1200 55 L1200 68 Q600 160 0 72Z" fill="#3b6ef2"/>
</svg>
<div class="abs mouse"><svg width="22" height="32" viewBox="0 0 22 32" fill="none" stroke="#3b6ef2" stroke-width="2"><rect x="2" y="2" width="18" height="28" rx="9"/><path d="M11 9v9M7.5 15l3.5 3.5 3.5-3.5"/></svg></div>

<!-- about -->
<section class="about">
  <div class="abs photo about-main" role="img" aria-label="Hands using a phone and laptop over engineering drawings"></div>
  <div class="abs photo about-small" role="img" aria-label="Portrait of the chief engineer"></div>
  <div class="abs about-badge"></div>
  <h2 class="abs">About Me</h2>
  <div class="eyebrow-mark"><b></b><i></i></div>
  <p class="abs">Owen Hartley is the Chief Engineer at Valtorix Mechanical Design. He has 11 years experience working as a mechanical design engineer in multiple industries including high performance automotive, consumer products, medical, industrial plus many more. He has worked in multiple roles across a wide range of products.</p>
  <div class="abs ticks">
    <span><i class="tick"><svg width="10" height="10" viewBox="0 0 10 10" fill="none" stroke="#fff" stroke-width="1.8"><path d="M1.5 5l2.5 2.5 4.5-5"/></svg></i>15+ Years Experience</span>
    <span><i class="tick"><svg width="10" height="10" viewBox="0 0 10 10" fill="none" stroke="#fff" stroke-width="1.8"><path d="M1.5 5l2.5 2.5 4.5-5"/></svg></i>Manufacturing Focus</span>
  </div>
  <a class="abs pill dark">Tell us about your ideas<span class="ring"><svg><use href="#i-phone"/></svg></span></a>
</section>

<!-- services -->
<section class="abs band" style="top:1297px;height:730px"></section>
<h2 class="abs sec-title" style="top:1400px">What We Do You</h2>
<div class="abs sec-mark" style="top:1444px"><div class="eyebrow-mark"><i></i><b></b><i></i></div></div>
<p class="abs sec-sub" style="top:1484px">End-to-end mechanical design services engineered for manufacturability.</p>

<article class="abs card svc" style="left:141px">
  <div class="ico"><svg viewBox="0 0 32 32"><path d="M16 4l11 6v12l-11 6-11-6V10z M5 10l11 6 11-6 M16 16v12"/></svg></div>
  <h3>Bespoke Product Design</h3>
  <p>Innovative design from concept<br>through the full development life cycle</p>
  <div class="img" style="background:linear-gradient(135deg,#e7e3dc,#b9ad9e 55%,#6f6558)" role="img" aria-label="Design team meeting around a table"></div>
</article>
<article class="abs card svc" style="left:458px">
  <div class="ico dark"><svg viewBox="0 0 32 32"><rect x="5" y="6" width="22" height="20" rx="2"/><path d="M10 11h12v10H10z"/></svg></div>
  <h3>3D Modelling and Drawings</h3>
  <p>We create 3D CAD, 2D engineering<br>drawings &amp; photorealistic render</p>
  <div class="img" style="background:linear-gradient(135deg,#9ea3a8,#5d6368 55%,#2f3337)" role="img" aria-label="Tablet showing a 3D model render"></div>
</article>
<article class="abs card svc" style="left:776px">
  <div class="ico"><svg viewBox="0 0 32 32"><circle cx="16" cy="16" r="5"/><circle cx="16" cy="16" r="11" stroke-dasharray="4 3"/></svg></div>
  <h3>Design for Manufacture</h3>
  <p>Creating designs optimised for<br>prototype and production manufacture</p>
  <div class="img" style="background:linear-gradient(135deg,#d9e2ec,#8ea4bd 55%,#4a6079)" role="img" aria-label="Production line in a manufacturing facility"></div>
</article>

<!-- case studies -->
<h2 class="abs sec-title" style="top:2079px">Our Work &amp; Case Studies</h2>
<div class="abs sec-mark" style="top:2122px"><div class="eyebrow-mark"><i></i><b></b><i></i></div></div>
<p class="abs sec-sub" style="top:2163px">A selection of engineering and product design projects demonstrating precision and performance.</p>

<article class="abs card case" style="left:141px">
  <div class="img" role="img" aria-label="Render of an industrial assembly frame"></div>
  <h3>Industrial Assembly System</h3>
  <p>Complete redesign of automated assembly<br>line components for manufacturing efficiency<br>improvement.</p>
  <a class="more">View Case Study <svg><use href="#i-arrow"/></svg></a>
</article>
<article class="abs card case" style="left:458px">
  <div class="img" role="img" aria-label="Render of a three piece alloy wheel"></div>
  <h3>3-Piece Alloy Wheels</h3>
  <p>Lightweight suspension component design<br>with FEA validation for high-performance<br>vehicle application.</p>
  <a class="more">View Case Study <svg><use href="#i-arrow"/></svg></a>
</article>
<article class="abs card case" style="left:776px">
  <div class="img" role="img" aria-label="Render of a portable medical device enclosure"></div>
  <h3>Medical Device Enclosure</h3>
  <p>Ergonomic and manufacturable enclosure<br>design for a portable medical diagnostic<br>device.</p>
  <a class="more">View Case Study <svg><use href="#i-arrow"/></svg></a>
</article>
<a class="abs pill blue" style="left:497px;top:2591px;width:206px;height:44px;font-size:13px">View All Case Study<span class="ring"><svg><use href="#i-phone"/></svg></span></a>

<!-- process -->
<section class="abs band" style="top:2703px;height:585px"></section>
<h2 class="abs sec-title" style="top:2806px">How We Work</h2>
<div class="abs sec-mark" style="top:2849px"><div class="eyebrow-mark"><i></i><b></b><i></i></div></div>
<p class="abs sec-sub" style="top:2890px">A selection of engineering and product design projects demonstrating precision and performance.</p>

<article class="abs card step" style="left:133px">
  <div class="head"><span class="ico"><svg viewBox="0 0 24 24"><path d="M4 5h16v11H9l-5 4z"/></svg></span>Consultation</div>
  <p>We begin with comprehensive<br>consultation to understand<br>your technical requirements,<br>constraints, &amp; objectives.</p>
  <span class="num">01</span><a class="more">Find out more <svg><use href="#i-arrow"/></svg></a>
</article>
<article class="abs card step" style="left:374px">
  <div class="head"><span class="ico"><svg viewBox="0 0 24 24"><rect x="3" y="4" width="18" height="13" rx="1"/><path d="M8 21h8M12 17v4"/></svg></span>Design</div>
  <p>Development of initial<br>concepts, 3D models, and<br>functional prototypes for<br>evaluation and refinement.</p>
  <span class="num">02</span><a class="more">Find out more <svg><use href="#i-arrow"/></svg></a>
</article>
<article class="abs card step" style="left:614px">
  <div class="head"><span class="ico"><svg viewBox="0 0 24 24"><circle cx="12" cy="12" r="9"/><path d="M8 12l3 3 5-6"/></svg></span>Validation</div>
  <p>Rigorous testing and analysis<br>including FEA, CFD, and<br>tolerance analysis to validate<br>design performance.</p>
  <span class="num">03</span><a class="more">Find out more <svg><use href="#i-arrow"/></svg></a>
</article>
<article class="abs card step" style="left:855px">
  <div class="head"><span class="ico"><svg viewBox="0 0 24 24"><path d="M12 3l8 4.5v9L12 21l-8-4.5v-9z M4 7.5l8 4.5 8-4.5 M12 12v9"/></svg></span>Delivery</div>
  <p>Creation of comprehensive<br>engineering drawings, Bill of<br>Materials, and manufacturing<br>documentation.</p>
  <span class="num">04</span><a class="more">Find out more <svg><use href="#i-arrow"/></svg></a>
</article>

<!-- testimonial -->
<section class="testimonial">
  <div class="abs arrow-btn" style="left:123px;top:3498px;background:#cfd3da"><svg viewBox="0 0 12 12"><path d="M8 2L4 6l4 4"/></svg></div>
  <div class="abs arrow-btn" style="left:1047px;top:3498px;background:var(--blue)"><svg viewBox="0 0 12 12"><path d="M4 2l4 4-4 4"/></svg></div>
  <h3 class="abs quote-name">Martin Delacroix</h3>
  <p class="abs quote-role">Project Manager AT Northfield</p>
  <span class="abs qmark" style="left:192px;top:3428px">&ldquo;</span>
  <p class="abs quote-text">"Owen went above and beyond in all aspects of the job. He identified issues with the design that I had not foreseen, rebuilt the design from scratch to ensure no aspect was overlooked, and provided solutions immediately to challenges he found. After some explaining about the end use of the product, he was able to offer ways to optimise the product further than I had thought.</p>
  <span class="abs qmark" style="left:694px;top:3574px">&rdquo;</span>
  <div class="abs portrait" role="img" aria-label="Portrait of the client giving the testimonial"></div>
  <div class="abs socials"><i class="round"></i><i class="round on"></i><i class="round"></i></div>
  <div class="abs dots"><i></i><i class="on"></i><i></i><i></i></div>
</section>

<!-- contact -->
<svg class="abs contact-bg" viewBox="0 0 1200 600" preserveAspectRatio="none">
  <path d="M0 0H1200V540Q600 590 0 545Z" fill="#3b6ef2"/>
</svg>
<section class="contact">
  <h2 class="abs">Start Your Journey With Us</h2>
  <p class="abs lead">Let's discuss your requirements and find the right solution.<br>Trusted by engineers, founders, and manufacturers.</p>
  <div class="abs line-item" style="top:4012px"><span class="c"><svg><use href="#i-phone"/></svg></span><div>Call Now<br>+44 (0) 7700 900418</div></div>
  <div class="abs line-item" style="top:4084px"><span class="c"><svg><use href="#i-mail"/></svg></span><div>Email Now<br>info@valtorix.design</div></div>
  <form class="abs form">
    <h3>Field The Below <span>Details</span></h3>
    <div class="field">First Name</div>
    <div class="field">Last Name</div>
    <div class="field">Email ID</div>
    <div class="field msg">Message</div>
    <div class="submit">Submit Your Details <svg><use href="#i-arrow"/></svg></div>
  </form>
</section>

<!-- footer -->
<footer class="abs footer">
  <div class="brand"><span class="dot"></span>valtorix</div>
  <p class="abs desc">Welcome to Valtorix Mechanical Design. We are a UK based design consultancy offering a comprehensive mechanical and product design service from initial concepts through to full volume production.</p>
  <nav class="abs fnav"><a>Home</a><a>About Us</a><a>Services</a><a>Our Work</a><a>Our Process</a></nav>
  <div class="abs fline"></div>
  <div class="abs fcontacts">
    <span><svg><use href="#i-pin"/></svg>We're based in South Wales, UK.</span>
    <span><svg><use href="#i-mail"/></svg>info@valtorix.design</span>
    <span><svg><use href="#i-phone"/></svg>+44 (0) 7700 900418</span>
  </div>
  <p class="abs copy">© 2025 Valtorix Mechanical Design</p>
  <div class="abs fsocial"><i></i><i></i><i class="on"></i><i></i></div>
</footer>
</body>
</html>
```